project - Misto Den

Dear designers, I'm Looking for an appealing new business card design to represent us for our new e-cigarette store: The MistO Den. Knowledgeable and friendly staff we aim for superior customer service with a positive atmosphere. Classic feel with modern touch is what we are aiming for . Lime green font and grey back round is the original color scheme but we are flexible and open to suggestions. I added some doodles to show you where my mind is at. address: 4827 203 St SW Edmonton, AB (inside the grand swap bazaar)web: themistoden.com email: info@themistoden.com phone : 555.214.6093 Thanks and am looking forward to seeing your creative , fresh and innovative designs.
Good luck everybody!
Gordon
Updates
lime green and charcoal grey please. thanks
Industry/Entity Type
Business
Logo Text
The MistO Den
Look and feel
Each slider illustrates characteristics of the customer's brand and the style your logo design should communicate.

```html
<!DOCTYPE html>
<html lang="en">
<head>
<meta charset="utf-8">
<title>The MistO Den – Business Card</title>
<link rel="stylesheet" href="https://fonts.googleapis.com/css2?family=Cinzel:wght@400&family=Open+Sans:wght@400;600&display=swap">
<style>
  :root {
    --backdrop: #2a2c2b;
    --charcoal: #5b5d5c;
    --charcoal-dark: #4e504f;
    --lime: #7cc242;
    --lime-light: #b9dd8e;
    --paper: #ffffff;
    --ink: #4a4c4b;
  }
  * { margin: 0; padding: 0; box-sizing: border-box; }
  html, body { width: 1200px; height: 898px; overflow: hidden; background: var(--backdrop); }
  .canvas { position: relative; width: 1200px; height: 898px; }
  .card {
    position: absolute; top: 294px; width: 540px; height: 309px; overflow: hidden;
    box-shadow: 0 12px 30px rgba(0,0,0,.45);
  }
  .card--front { left: 40px; background: linear-gradient(135deg, #656766 0%, var(--charcoal-dark) 100%); }
  .card--back { left: 620px; background: var(--paper); }

  .wordmark {
    position: absolute; font-family: "Cinzel", Georgia, serif; font-weight: 400;
    letter-spacing: 1px; white-space: nowrap; line-height: 1;
  }
  .card--front .wordmark { left: 0; right: 0; top: 128px; text-align: center; font-size: 54px; color: var(--lime); }
  .card--back .wordmark { left: 26px; top: 92px; font-size: 42px; color: var(--ink); }

  .band { position: absolute; left: 0; width: 100%; }
  .band--accent { top: 150px; height: 9px; background: var(--lime-light); }
  .band--lime { top: 159px; height: 38px; background: var(--lime); }
  .band--charcoal { top: 197px; height: 75px; background: var(--charcoal); }

  .person { position: absolute; left: 285px; top: 164px; color: var(--paper); font-family: "Open Sans", Arial, sans-serif; line-height: 1.1; }
  .person__name { font-size: 15px; font-weight: 600; letter-spacing: 1px; }
  .person__title { font-size: 8px; letter-spacing: 1px; }

  .contact-panel { position: absolute; left: 228px; top: 208px; width: 290px; height: 72px; }
  .contact-panel svg { position: absolute; inset: 0; }
  .contact {
    position: absolute; right: 18px; top: 8px; text-align: right; list-style: none;
    font-family: "Open Sans", Arial, sans-serif; font-size: 9px; line-height: 13.5px; color: var(--paper);
  }
</style>
</head>
<body>
<main class="canvas">
  <section class="card card--front" aria-label="Card front">
    <div class="wordmark">MISTO DEN</div>
  </section>

  <section class="card card--back" aria-label="Card back">
    <div class="wordmark">MISTO DEN</div>
    <div class="band band--accent"></div>
    <div class="band band--lime"></div>
    <div class="band band--charcoal"></div>
    <div class="person">
      <div class="person__name">ALAN REYES</div>
      <div class="person__title">GENERAL MANAGER</div>
    </div>
    <div class="contact-panel">
      <svg width="290" height="72" viewBox="0 0 290 72" aria-hidden="true">
        <polygon points="14,0 290,0 290,72 0,72" fill="var(--lime)"/>
      </svg>
      <ul class="contact">
        <li>014 372 5581</li>
        <li>alan@inboxmail.com</li>
        <li>www.themistoden.com</li>
        <li>4827 203 St SW Edmonton AB</li>
      </ul>
    </div>
  </section>
</main>
</body>
</html>
```